A revolutionary website for a revolutionary construction company

I am looking for inspirations... please help me and read the attached brief

I would like to achieve a website design that is modern, premium dynamic and drives emotions. I do not want a design that can be found on a normal template. Having that said, I would also like the utilisation of Illustrations that are relation to the company’s services…. Also would like to have illustrations dynamic when you navigate on them. So a young, dynamic and parallax design website that will show off these requirements. Also to add trust, with all pages designed.

please see attachements.
Updates

Low design quality

Target Market(s)

Please read brief

Number of Pages Required

5+ page

Font styles to use
Other font styles liked:
• Futura

Requirements
Must have
• Please read brief - colours to be matching logo colours
Nice to have
Should not have

```html
<!DOCTYPE html>
<html lang="en">
<head>
<meta charset="utf-8">
<title>Keystone Works — Built on steady ground</title>
<link href="https://fonts.googleapis.com/css2?family=IBM+Plex+Sans:wght@400;500;700&display=swap" rel="stylesheet">
<style>
:root{
  --maroon:#7a0f2e;
  --ink:#231f20;
  --charcoal:#4b4345;
  --text:#3b3536;
  --muted:#6b6466;
  --blush:#f4efef;
  --line:#d9d4d5;
  --white:#ffffff;
}
*{box-sizing:border-box;margin:0;padding:0}
html,body{width:1200px;height:4878px;overflow:hidden}
body{position:relative;background:var(--white);font-family:"IBM Plex Sans",Arial,sans-serif;color:var(--text)}
.abs{position:absolute}
.btn{position:absolute;display:flex;align-items:center;justify-content:center;background:var(--maroon);color:var(--white);font-size:14px;letter-spacing:.3px;text-transform:uppercase}
.section-title{position:absolute;left:0;width:1200px;text-align:center;font-weight:700;font-size:24px;letter-spacing:.5px;color:var(--ink)}
.section-title::after{content:"";display:block;width:52px;height:3px;background:var(--maroon);margin:14px auto 0}
.section-title.light{color:var(--white)}
.section-title.light::after{background:var(--white)}

/* header */
.site-header{position:absolute;left:0;top:0;width:1200px;height:118px;background:var(--white)}
.brand{position:absolute;left:133px;top:30px;display:flex;align-items:center;gap:12px}
.brand-mark{width:44px;height:44px;border:3px solid var(--charcoal);border-radius:50%;flex:none}
.brand-name{font-size:22px;font-weight:700;color:var(--maroon);line-height:26px}
.brand-tag{font-size:12px;color:var(--muted);line-height:16px}
.follow{position:absolute;left:695px;top:38px;font-size:10px;font-weight:700;color:var(--ink);letter-spacing:.4px}
.social-dot{position:absolute;top:32px;width:25px;height:25px;border-radius:50%;background:var(--maroon)}
.call-label{position:absolute;left:944px;top:24px;font-size:10px;font-weight:700;color:var(--ink)}
.call-number{position:absolute;left:944px;top:37px;font-size:20px;font-weight:500;color:var(--maroon)}
.main-nav{position:absolute;right:130px;top:82px;display:flex;gap:25px;font-size:13px;font-weight:500;color:var(--ink)}
.main-nav .active{color:var(--maroon);text-decoration:underline;text-underline-offset:4px}

/* hero */
.hero{position:absolute;left:0;top:118px;width:1200px;height:594px;background:linear-gradient(180deg,#c9ccd0 0%,#8e949b 45%,#5b6168 100%)}
.hero h1{position:absolute;top:176px;width:1200px;text-align:center;font-size:42px;font-weight:700;color:var(--white);letter-spacing:.5px}
.hero p{position:absolute;top:240px;width:1200px;text-align:center;font-size:18px;font-weight:700;line-height:24px;color:var(--white)}
.hero-dots{position:absolute;top:534px;left:558px;display:flex;gap:13px}
.hero-dots span{width:7px;height:7px;border-radius:50%;background:var(--white)}
.hero-dots span.on{background:var(--maroon)}

/* services */
.service-card{position:absolute;width:283px;height:343px;background:var(--white);border:1px solid var(--line)}
.service-card .photo{height:174px}
.service-card h3{position:absolute;left:25px;top:196px;font-size:13px;font-weight:700;color:var(--ink)}
.service-card p{position:absolute;left:25px;top:224px;width:240px;font-size:11.5px;line-height:17px;color:var(--text)}
.service-card .btn{left:25px;top:290px;width:85px;height:26px;font-size:10px}
.service-all{position:absolute;background:linear-gradient(180deg,#2c2728,#1f1b1c)}

/* welcome */
.welcome{position:absolute;left:0;top:1594px;width:1200px;height:443px;background:var(--blush)}
.welcome-photo{position:absolute;left:159px;top:51px;width:348px;height:348px;border-radius:50%;border:2px solid var(--maroon);padding:9px}
.welcome-photo div{width:100%;height:100%;border-radius:50%;background:linear-gradient(180deg,#2f6fc0 0%,#7fb1e4 50%,#c9b9a8 75%,#6e8a4a 100%)}
.welcome .kicker{position:absolute;left:586px;top:56px;font-size:18px;font-weight:700;color:var(--ink)}
.welcome h2{position:absolute;left:586px;top:76px;font-size:36px;font-weight:700;color:var(--ink);letter-spacing:.5px}
.welcome p{position:absolute;left:586px;top:162px;width:470px;font-size:14.5px;line-height:21.5px;color:var(--text)}

/* why */
.why{position:absolute;left:0;top:2037px;width:1200px;height:517px;background:linear-gradient(180deg,#eef0f2,#e2e5e8)}
.why-item{position:absolute;width:190px}
.why-item h4{font-size:14px;font-weight:700;color:var(--ink);margin-bottom:8px}
.why-item p{font-size:12px;line-height:16px;color:var(--text)}
.why-rule{position:absolute;height:1px;background:#c4c2c3}
.why-ring{position:absolute;left:458px;top:151px;width:284px;height:284px;border:7px solid var(--charcoal);border-radius:50%}

/* process */
.process{position:absolute;left:0;top:2554px;width:1200px;height:522px;background:var(--charcoal);color:var(--white)}
.step{position:absolute;top:140px;width:290px;text-align:center}
.step svg{display:block;margin:0 auto}
.step h4{margin-top:38px;font-size:18px;font-weight:700;letter-spacing:.5px}
.step p{margin-top:10px;font-size:14px;line-height:19px;color:#eee}

/* projects */
.project{position:absolute;top:3214px;width:282px;height:279px}

/* industries */
.industries{position:absolute;left:0;top:3640px;width:1200px;height:367px;background:#f2f2f3}
.industry{position:absolute;top:148px;width:219px;height:168px;background:var(--white);box-shadow:0 4px 12px rgba(0,0,0,.08);text-align:center}
.industry svg{display:block;margin:34px auto 0}
.industry span{display:block;margin-top:16px;font-size:15px;color:var(--ink)}

/* testimonials */
.testimonials{position:absolute;left:0;top:4007px;width:1200px;height:513px;background:linear-gradient(180deg,#3f3b3c,#5b5758)}
.quote-card{position:absolute;top:173px;width:297px;height:291px;background:var(--white);text-align:center}
.quote-mark{position:absolute;left:124px;top:-24px;width:48px;height:48px;border-radius:50%;background:var(--white);font-family:Georgia,serif;font-size:40px;font-weight:700;color:var(--charcoal);line-height:60px}
.quote-card p{position:absolute;left:36px;top:50px;width:225px;font-size:12.5px;line-height:19px;color:var(--text)}
.quote-card hr{position:absolute;left:128px;top:242px;width:40px;border:0;border-top:1px solid #aaa}
.quote-card .who{position:absolute;top:254px;width:297px;font-size:10px;color:var(--text)}
.quote-card .who b{font-weight:700;color:var(--ink)}

/* footer */
.site-footer{position:absolute;left:0;top:4520px;width:1200px;height:358px;background:var(--ink);color:#d8d4d5}
.footer-brand{position:absolute;left:140px;top:110px;display:flex;align-items:center;gap:14px}
.footer-brand .brand-mark{width:54px;height:54px;border-color:#8e8889}
.footer-brand .brand-name{font-size:24px;color:#e4e0e1;line-height:28px}
.footer-brand .brand-tag{font-size:13px;color:#b7b1b2}
.footer-col h5{font-size:12px;font-weight:700;color:var(--white);margin-bottom:18px;letter-spacing:.4px}
.footer-col li{list-style:none;font-size:11px;line-height:20px;color:#d8d4d5}
.contact-row{position:relative;padding-left:32px;font-size:11px;line-height:14px;margin-bottom:22px}
.contact-row .ico{position:absolute;left:0;top:2px;width:24px;height:24px;border-radius:50%;background:var(--white)}
.copyright{position:absolute;top:312px;width:1200px;text-align:center;font-size:9px;color:#cfcacb}
</style>
</head>
<body>

<header class="site-header">
  <div class="brand">
    <div class="brand-mark"></div>
    <div>
      <div class="brand-name">Keystone Works</div>
      <div class="brand-tag">Built on steady ground</div>
    </div>
  </div>
  <div class="follow">FOLLOW US</div>
  <span class="social-dot" style="left:777px"></span>
  <span class="social-dot" style="left:810px"></span>
  <span class="social-dot" style="left:843px"></span>
  <svg class="abs" style="left:903px;top:30px" width="30" height="30" viewBox="0 0 24 24" fill="none" stroke="#231f20" stroke-width="1.6"><path d="M5 3h4l2 5-2.5 1.5a11 11 0 0 0 6 6L16 13l5 2v4a2 2 0 0 1-2 2A16 16 0 0 1 3 5a2 2 0 0 1 2-2z"/><path d="M15 3a6 6 0 0 1 6 6M15 6.5a3 3 0 0 1 2.5 2.5"/></svg>
  <div class="call-label">CALL US</div>
  <div class="call-number">555.014.2290</div>
  <nav class="main-nav">
    <span class="active">HOME</span><span>ABOUT US</span><span>SERVICES</span><span>PROCESS</span><span>INDUSTRIES</span><span>TESTIMONIALS</span><span>CONTACT US</span>
  </nav>
</header>

<section class="hero" role="img" aria-label="Photo of a bright modern open-plan office with glass partitions and desks">
  <h1>OFFICE RENOVATION</h1>
  <p>LOREM IPSUM DOLOR SIT AMET CONSECTETUR<br>ADIPISCING ELIT SED DO EIUSMOD</p>
  <div class="btn" style="left:532px;top:312px;width:136px;height:48px;font-size:15px">Read More</div>
  <div class="hero-dots"><span></span><span></span><span class="on"></span><span></span><span></span></div>
</section>

<h2 class="section-title" style="top:750px">OUR SERVICES</h2>

<article class="service-card" style="left:160px;top:835px">
  <div class="photo" role="img" aria-label="Photo of a fitted-out office interior" style="background:linear-gradient(180deg,#dfe4ea,#8d8f93)"></div>
  <h3>FIT-OUT</h3>
  <p>Lorem ipsum dolor sit amet, cons ect etur adipiscing elit sed do eiusm od tempor incididunt</p>
  <div class="btn">Read More</div>
</article>
<article class="service-card" style="left:460px;top:835px">
  <div class="photo" role="img" aria-label="Illustration of a modern house design with sketch lines" style="background:linear-gradient(180deg,#e8ecef,#9fb28a)"></div>
  <h3>DESIGN AND CONSTRUCT</h3>
  <p>Lorem ipsum dolor sit amet, cons ect etur adipiscing elit sed do eiusm od tempor incididunt</p>
  <div class="btn">Read More</div>
</article>
<article class="service-card" style="left:759px;top:835px">
  <div class="photo" role="img" aria-label="Photo of cranes over a building under construction" style="background:linear-gradient(180deg,#3b86d6,#c9c3b8)"></div>
  <h3>CONSTRUCTION</h3>
  <p>Lorem ipsum dolor sit amet, cons ect etur adipiscing elit sed do eiusm od tempor incididunt</p>
  <div class="btn">Read More</div>
</article>
<article class="service-card" style="left:160px;top:1196px">
  <div class="photo" role="img" aria-label="Photo looking up at city towers at dusk" style="background:linear-gradient(180deg,#2d3548,#b0643a)"></div>
  <h3>PROJECT MANAGEMENT</h3>
  <p>Lorem ipsum dolor sit amet, cons ect etur adipiscing elit sed do eiusm od tempor incididunt</p>
  <div class="btn">Read More</div>
</article>
<article class="service-card" style="left:460px;top:1196px">
  <div class="photo" role="img" aria-label="Photo of an office worker taking a phone call at a desk" style="background:linear-gradient(180deg,#e9eaec,#a7a9ad)"></div>
  <h3>24-HR SERVICE CALLS</h3>
  <p>Lorem ipsum dolor sit amet, cons ect etur adipiscing elit sed do eiusm od tempor incididunt</p>
  <div class="btn">Read More</div>
</article>
<div class="service-all" style="left:759px;top:1196px;width:283px;height:343px">
  <div class="btn" style="left:53px;top:150px;width:188px;height:44px">View All Services</div>
</div>

<section class="welcome">
  <div class="welcome-photo"><div role="img" aria-label="Photo of a modern school building under a blue sky"></div></div>
  <div class="kicker">WELCOME TO</div>
  <h2>KEYSTONE WORKS</h2>
  <p>Sed ut perspiciatis unde omnis iste natus error sit voluptatem accusantium doloremque laudantium, totam rem aperiam, eaque ipsa quae ab illo inventore veritatis et quasi architecto beatae vitae dicta sunt explicabo. Nemo enim ipsam voluptatem quia voluptas sit aspernatur aut odit aut fugit, sed quia consequuntur magni dolores eos qui ratione voluptatem sequi nesciunt. Neque porro quisquam est, qui dolorem ipsum quia dolor sit amet, consectetur</p>
  <div class="btn" style="left:586px;top:343px;width:112px;height:36px;font-size:13px">Read More</div>
</section>

<section class="why">
  <h2 class="section-title" style="top:49px">WHY CHOOSE US</h2>
  <svg class="abs" style="left:130px;top:166px" width="70" height="70" viewBox="0 0 70 70"><circle cx="35" cy="35" r="30" fill="var(--maroon)"/><circle cx="42" cy="40" r="24" fill="none" stroke="#fff" stroke-width="3"/></svg>
  <div class="why-item" style="left:236px;top:164px"><h4>TRANSPARENCY</h4><p>Sed ut perspiciatis unde omnis iste natus error sit voluptatem accusantium doloremque laud antium, totam rem aperiam, eaque ipsa quae ab illo.</p></div>
  <svg class="abs" style="left:136px;top:330px" width="60" height="66" viewBox="0 0 60 66"><circle cx="30" cy="16" r="13" fill="var(--maroon)"/><path d="M4 64c0-18 11-30 26-30s26 12 26 30z" fill="var(--maroon)"/><path d="M30 36l-4 6 4 16 4-16z" fill="#fff"/></svg>
  <div class="why-item" style="left:236px;top:325px"><h4>PROFESSIONALISM</h4><p>Sed ut perspiciatis unde omnis iste natus error sit voluptatem accusantium doloremque laud antium, totam rem aperiam, eaque ipsa quae ab illo.</p></div>
  <div class="why-item" style="left:793px;top:164px"><h4>QUALITY SERVICES</h4><p>Sed ut perspiciatis unde omnis iste natus error sit voluptatem accusantium doloremque laud antium, totam rem aperiam, eaque ipsa quae ab illo.</p></div>
  <svg class="abs" style="left:996px;top:168px" width="72" height="72" viewBox="0 0 72 72"><g fill="var(--maroon)"><circle cx="36" cy="6" r="3"/><circle cx="58" cy="14" r="3"/><circle cx="66" cy="36" r="3"/><circle cx="58" cy="58" r="3"/><circle cx="36" cy="66" r="3"/><circle cx="14" cy="58" r="3"/><circle cx="6" cy="36" r="3"/><circle cx="14" cy="14" r="3"/><rect x="22" y="34" width="7" height="16"/><path d="M31 34l6-12c3 0 5 2 4 6l-1 5h9c3 0 4 3 3 5l-4 11c-1 1-2 1-3 1H31z"/></g></svg>
  <div class="why-item" style="left:793px;top:325px"><h4>TRUST</h4><p>Sed ut perspiciatis unde omnis iste natus error sit voluptatem accusantium doloremque laud antium, totam rem aperiam, eaque ipsa quae ab illo.</p></div>
  <svg class="abs" style="left:1008px;top:330px" width="60" height="68" viewBox="0 0 60 68"><path d="M30 3l25 9v20c0 17-11 28-25 33C16 60 5 49 5 32V12z" fill="none" stroke="var(--maroon)" stroke-width="5"/><circle cx="30" cy="34" r="12" fill="var(--maroon)"/><path d="M24 34l4 4 8-8" fill="none" stroke="#fff" stroke-width="3"/></svg>
  <div class="why-rule" style="left:133px;top:303px;width:282px"></div>
  <div class="why-rule" style="left:785px;top:303px;width:285px"></div>
  <div class="why-ring"></div>
</section>

<section class="process">
  <h2 class="section-title light" style="top:47px">OUR WORK PROCESS</h2>
  <div class="step" style="left:122px">
    <svg width="90" height="80" viewBox="0 0 90 80" fill="none" stroke="#fff" stroke-width="2.5"><rect x="10" y="10" width="72" height="54"/><path d="M10 10c-6 0-8 4-8 8v50c0-4 3-6 8-6M22 20h48v34H22zM36 20v34M36 36h34M50 70h30"/></svg>
    <h4>PLAN</h4>
    <p>Sed ut perspiciatis unde omnis iste natus error sit voluptatem accusantium dolore mque laud antium, totam rem ape riam, eaque ipsa quae ab illo.</p>
  </div>
  <div class="step" style="left:456px">
    <svg width="90" height="80" viewBox="0 0 90 80"><g fill="none" stroke="#fff" stroke-width="8" stroke-dasharray="6 4"><circle cx="52" cy="32" r="20"/><circle cx="24" cy="58" r="11"/></g><circle cx="52" cy="32" r="8" fill="#fff"/><circle cx="24" cy="58" r="4" fill="#fff"/></svg>
    <h4>EXECUTION</h4>
    <p>Sed ut perspiciatis unde omnis iste natus error sit voluptatem accusantium dolore mque laud antium, totam rem ape riam, eaque ipsa quae ab illo.</p>
  </div>
  <div class="step" style="left:796px">
    <svg width="90" height="80" viewBox="0 0 90 80" fill="#fff"><rect x="12" y="8" width="44" height="70"/><rect x="56" y="28" width="24" height="50"/><g fill="var(--charcoal)"><rect x="18" y="16" width="8" height="8"/><rect x="31" y="16" width="8" height="8"/><rect x="44" y="16" width="8" height="8"/><rect x="18" y="30" width="8" height="8"/><rect x="31" y="30" width="8" height="8"/><rect x="44" y="30" width="8" height="8"/><rect x="18" y="44" width="8" height="8"/><rect x="44" y="44" width="8" height="8"/><rect x="28" y="60" width="12" height="18"/><rect x="62" y="36" width="6" height="6"/><rect x="62" y="50" width="6" height="6"/></g></svg>
    <h4>HANDOVER</h4>
    <p>Sed ut perspiciatis unde omnis iste natus error sit voluptatem accusantium dolore mque laud antium, totam rem ape riam, eaque ipsa quae ab illo.</p>
  </div>
  <div class="btn" style="left:535px;top:418px;width:148px;height:46px;border:2px solid #fff">Contact Us</div>
</section>

<h2 class="section-title" style="top:3118px">PAST PROJECTS</h2>
<div class="project" style="left:15px;background:linear-gradient(180deg,#5f8fd0 0%,#c9a87a 45%,#6d6a66 100%)" role="img" aria-label="Photo of a school gymnasium entrance"></div>
<div class="project" style="left:311px;background:linear-gradient(180deg,#f0f0f0,#8a8c90)" role="img" aria-label="Photo of a long polished school corridor"></div>
<div class="project" style="left:607px;background:linear-gradient(180deg,#3a78d0 0%,#a0553c 55%,#5f7040 100%)" role="img" aria-label="Photo of a brick university hall with a clock tower"></div>
<div class="project" style="left:903px;background:linear-gradient(180deg,#aacaef 0%,#c9b096 50%,#6f8a3a 100%)" role="img" aria-label="Photo of a modern brick school building"></div>
<div class="btn" style="left:512px;top:3548px;width:176px;height:38px;font-size:13px">View All Projects</div>

<section class="industries">
  <h2 class="section-title" style="top:48px">INDUSTRIES</h2>
  <div class="industry" style="left:133px"><svg width="56" height="56" viewBox="0 0 56 56" fill="var(--maroon)"><rect x="8" y="6" width="26" height="46"/><rect x="34" y="20" width="16" height="32"/><g fill="#fff"><rect x="13" y="12" width="5" height="5"/><rect x="24" y="12" width="5" height="5"/><rect x="13" y="22" width="5" height="5"/><rect x="24" y="22" width="5" height="5"/><rect x="13" y="32" width="5" height="5"/><rect x="24" y="32" width="5" height="5"/><rect x="18" y="42" width="7" height="10"/><rect x="39" y="26" width="5" height="5"/><rect x="39" y="36" width="5" height="5"/></g></svg><span>OFFICES</span></div>
  <div class="industry" style="left:371px"><svg width="56" height="56" viewBox="0 0 56 56" fill="var(--maroon)"><rect x="27" y="2" width="2" height="12"/><rect x="29" y="2" width="10" height="6"/><path d="M6 26L28 12l22 14z"/><rect x="8" y="26" width="40" height="26"/><g fill="#fff"><rect x="13" y="31" width="30" height="4"/><rect x="24" y="40" width="8" height="12"/><rect x="13" y="40" width="6" height="6"/><rect x="37" y="40" width="6" height="6"/></g></svg><span>SCHOOLS</span></div>
  <div class="industry" style="left:609px"><svg width="56" height="56" viewBox="0 0 56 56" fill="var(--maroon)"><path d="M6 20l4-14h36l4 14z"/><rect x="9" y="20" width="38" height="32"/><g fill="#fff"><rect x="14" y="28" width="12" height="24"/><rect x="31" y="28" width="11" height="10"/><rect x="15" y="21" width="4" height="4"/><rect x="26" y="21" width="4" height="4"/><rect x="37" y="21" width="4" height="4"/></g></svg><span>RETAIL</span></div>
  <div class="industry" style="left:847px"><svg width="56" height="56" viewBox="0 0 56 56" fill="var(--maroon)"><rect x="10" y="4" width="36" height="48"/><g fill="#fff"><rect x="15" y="10" width="6" height="6"/><rect x="25" y="10" width="6" height="6"/><rect x="35" y="10" width="6" height="6"/><rect x="15" y="21" width="6" height="6"/><rect x="25" y="21" width="6" height="6"/><rect x="35" y="21" width="6" height="6"/><rect x="15" y="32" width="6" height="6"/><rect x="35" y="32" width="6" height="6"/><rect x="24" y="40" width="8" height="12"/></g></svg><span>HOSPITALITY</span></div>
</section>

<section class="testimonials">
  <h2 class="section-title light" style="top:46px">TESTIMONIALS</h2>
  <div class="quote-card" style="left:133px"><div class="quote-mark">“</div><p>Lorem ipsum dolor sit amet, con sectetur adipiscing elit, sed do eius mod tempor incididunt ut labore et dolore magna aliqua. Ut enim ad min im veniam, quis nostrud exe rcitation ullamco laboris nisi ut aliquip ex ea commodo consequat. Duis aute irure dolor in reprehenderit.</p><hr><div class="who"><b>MARTIN</b> Leeds</div></div>
  <div class="quote-card" style="left:454px"><div class="quote-mark">“</div><p>Lorem ipsum dolor sit amet, con sectetur adipiscing elit, sed do eius mod tempor incididunt ut labore et dolore magna aliqua. Ut enim ad min im veniam, quis nostrud exe rcitation ullamco laboris nisi ut aliquip ex ea commodo consequat. Duis aute irure dolor in reprehenderit.</p><hr><div class="who"><b>MARTIN</b> Leeds</div></div>
  <div class="quote-card" style="left:774px"><div class="quote-mark">“</div><p>Lorem ipsum dolor sit amet, con sectetur adipiscing elit, sed do eius mod tempor incididunt ut labore et dolore magna aliqua. Ut enim ad min im veniam, quis nostrud exe rcitation ullamco laboris nisi ut aliquip ex ea commodo consequat. Duis aute irure dolor in reprehenderit.</p><hr><div class="who"><b>MARTIN</b> Leeds</div></div>
</section>

<footer class="site-footer">
  <div class="footer-brand">
    <div class="brand-mark"></div>
    <div>
      <div class="brand-name">Keystone Works</div>
      <div class="brand-tag">Built on steady ground</div>
    </div>
  </div>
  <div class="footer-col abs" style="left:493px;top:54px">
    <h5>MENU</h5>
    <ul><li>HOME</li><li>ABOUT US</li><li>SERVICES</li><li>PROCESS</li><li>INDUSTRIES</li><li>TESTIMONIALS</li><li>CONTACT US</li></ul>
  </div>
  <div class="footer-col abs" style="left:688px;top:54px;width:200px">
    <h5>CONTACT US</h5>
    <div class="contact-row"><svg class="ico" viewBox="0 0 24 24"><circle cx="12" cy="12" r="12" fill="#fff"/><path d="M12 6a4 4 0 0 0-4 4c0 3 4 8 4 8s4-5 4-8a4 4 0 0 0-4-4z" fill="var(--ink)"/><circle cx="12" cy="10" r="1.5" fill="#fff"/></svg>2150 Alder Lane<br>Fairview, CA 90210</div>
    <div class="contact-row"><svg class="ico" viewBox="0 0 24 24"><circle cx="12" cy="12" r="12" fill="#fff"/><path d="M8 7h2l1 3-1.5 1a6 6 0 0 0 3.5 3.5l1-1.5 3 1v2a1 1 0 0 1-1 1A9 9 0 0 1 7 8a1 1 0 0 1 1-1z" fill="var(--ink)"/></svg>Call Us<br>555.014.2290</div>
    <div class="contact-row"><svg class="ico" viewBox="0 0 24 24"><circle cx="12" cy="12" r="12" fill="#fff"/><rect x="6" y="8" width="12" height="8" fill="var(--ink)"/><path d="M6 8l6 5 6-5" fill="none" stroke="#fff" stroke-width="1"/></svg>E mail Us<br>hello@keystoneworks.com</div>
  </div>
  <div class="footer-col abs" style="left:950px;top:54px;width:130px">
    <h5>FOLLOW US</h5>
    <div class="contact-row"><span class="ico"></span>Like us on<br>OUR PAGE</div>
    <div class="contact-row"><span class="ico"></span>Follow us on<br>OUR NEWS</div>
    <div class="contact-row"><span class="ico"></span>Follow us on<br>OUR NETWORK</div>
  </div>
  <div class="copyright">Copyright © 2020 All Rights Reserved</div>
</footer>

</body>
</html>
```